Stonebrace Business Card Design

The Stonebrace Co is an aggregate (crushing) equipment dealer serving Western Canadian provinces. Stonebrace is a distributor of aggregate equipment for different manufacturers.

We are looking to change and update the existing business card which has been used since the existence of the company. A copy of existing card has been attached for reference. The Stonebrace Co logo we want to remain the same and we want the green color to remain the same.

We are wanting something new with a different look. A refreshing card to show a new modern and updated look. No longer wanting to have the manufacturers on the back of the card but something more like our logo on the back of the card with a statement like "Crushing Solutions"

ideas could be:
- card can be different colors on front and back
- front or reverse of the card could possibly be the green color with the logo in black

Target Market(s)

Owners of Aggregate/Crushing companies

Contact Information for Business Card

see above

Requirements
Must have
• - logo to remain same along with same font within logo
• - green color to remain same
Nice to have
• as noted above under project description
Should not have

```html
<!DOCTYPE html>
<html lang="en">
<head>
<meta charset="utf-8">
<title>Stonebrace Business Card</title>
<link href="https://fonts.googleapis.com/css2?family=Roboto:wght@400;500;700&display=swap" rel="stylesheet">
<style>
  :root {
    --stage: #6f4b34;
    --brand-green: #878a0b;
    --brand-green-dark: #6f7209;
    --ink: #231f20;
    --paper: #f3f3f3;
    --white: #ffffff;
  }
  * { margin: 0; padding: 0; box-sizing: border-box; }
  html, body { width: 1200px; height: 960px; overflow: hidden; }
  body {
    background: var(--stage);
    font-family: "Roboto", Arial, sans-serif;
    position: relative;
  }
  .card {
    position: absolute;
    width: 600px;
    border-radius: 22px;
    overflow: hidden;
  }
  .card-stack-under {
    left: 316px; top: 104px; height: 352px;
    background: var(--brand-green-dark);
    transform: rotate(-1.2deg);
    box-shadow: 0 6px 14px rgba(0,0,0,.45);
  }
  .card-front {
    left: 320px; top: 95px; height: 355px;
    background: var(--brand-green);
    box-shadow: 0 4px 10px rgba(0,0,0,.4);
  }
  .front-mark {
    position: absolute; left: 110px; top: 160px;
    display: flex; align-items: center; gap: 22px;
  }
  .mark-dot {
    width: 52px; height: 52px; border-radius: 50%;
    background: var(--ink);
  }
  .company-name {
    font-weight: 700; font-size: 22px; color: var(--ink);
    letter-spacing: .2px; white-space: nowrap;
  }
  .tagline {
    position: absolute; left: 0; right: 0; top: 304px;
    text-align: center; font-weight: 500; font-size: 15px; color: var(--ink);
  }
  .card-back {
    left: 320px; top: 493px; height: 342px;
    background: var(--paper);
    box-shadow: 0 4px 10px rgba(0,0,0,.4);
  }
  .back-mark-dot {
    position: absolute; left: 80px; top: 35px;
    width: 92px; height: 92px; border-radius: 50%;
    background: var(--brand-green);
  }
  .back-company {
    position: absolute; left: 34px; top: 144px;
    font-size: 21px;
  }
  .swoosh { position: absolute; left: 0; top: 0; }
  .person { position: absolute; left: 34px; top: 263px; }
  .person-name { font-weight: 700; font-size: 20px; color: var(--brand-green); }
  .person-role { font-size: 14px; color: var(--ink); margin-top: 3px; }
  .contact {
    position: absolute; right: 24px; top: 182px;
    color: var(--white); font-size: 14px; text-align: right;
    line-height: 19px;
  }
  .contact .address { margin-bottom: 10px; }
  .contact-line { display: flex; justify-content: flex-end; align-items: center; gap: 7px; }
  .contact-line svg { width: 12px; height: 12px; flex: none; }
</style>
</head>
<body>
  <div class="card card-stack-under"></div>

  <section class="card card-front">
    <div class="front-mark">
      <span class="mark-dot"></span>
      <span class="company-name">THE STONEBRACE CO.</span>
    </div>
    <p class="tagline">Crushing Solutions</p>
  </section>

  <section class="card card-back">
    <span class="back-mark-dot"></span>
    <p class="company-name back-company">THE STONEBRACE CO.</p>

    <svg class="swoosh" width="600" height="342" viewBox="0 0 600 342">
      <path d="M266 342 C320 220 440 130 600 118 L600 124 C450 140 340 230 284 342 Z" fill="var(--ink)"/>
      <path d="M284 342 C340 230 450 140 600 124 L600 342 Z" fill="var(--brand-green)"/>
    </svg>

    <div class="person">
      <p class="person-name">BRENT HALVORSEN</p>
      <p class="person-role">CEO/FOUNDER</p>
    </div>

    <div class="contact">
      <p class="address">2218- 71B Avenue<br>Redwater, Alberta T0A 2W0</p>
      <p class="contact-line">780.555.0142
        <svg viewBox="0 0 12 12"><path d="M2.5 1l2 2.2-1 1.2a6 6 0 0 0 4.1 4.1l1.2-1 2.2 2-1.2 1.5C5.5 11 1 6.5 1 2.2z" fill="#fff"/></svg></p>
      <p class="contact-line">780.555.0187
        <svg viewBox="0 0 12 12"><rect x="3" y="0.5" width="6" height="11" rx="1" fill="none" stroke="#fff" stroke-width="1.2"/><rect x="4.3" y="2" width="3.4" height="6.5" fill="#fff"/></svg></p>
      <p class="contact-line">780.555.0163
        <svg viewBox="0 0 12 12"><rect x="3" y="1" width="6" height="3" fill="#fff"/><rect x="1" y="4.5" width="10" height="5" rx="1" fill="#fff"/><rect x="3" y="8" width="6" height="3" fill="#fff" stroke="var(--brand-green)" stroke-width=".6"/></svg></p>
      <p class="contact-line">brent@stonebr.com
        <svg viewBox="0 0 12 12"><rect x="0.5" y="2.5" width="11" height="7.5" fill="#fff"/><path d="M0.5 2.8l5.5 4 5.5-4" fill="none" stroke="var(--brand-green)" stroke-width="1"/></svg></p>
      <p class="contact-line">www.stonebrace.ca
        <svg viewBox="0 0 12 12"><circle cx="6" cy="6" r="5.5" fill="#fff"/><path d="M6 .5v11M.5 6h11M6 .5c-3 3-3 8 0 11M6 .5c3 3 3 8 0 11" fill="none" stroke="var(--brand-green)" stroke-width=".8"/></svg></p>
    </div>
  </section>
</body>
</html>
```